Business card for my new company (Accounting firm)

I need a business card for my new business Brightwell Advisory and Ledger SA. Our services are accounting, tax, audit and financial management. Our customers are small companies, start-ups and new companies. The final design has to show financial security, trust and growth. Please find our logo attached to the business card. Text for the business card: Brightwell Advisory and Ledger SA Tomas Varenholt Director and Founder Certified Accountant Tel. 022 418 57 34 tv@clairevalconseil.ch www.clairevalconseil.ch Rue des Vergières 27 1201 Geneva
Target Market(s)
Our customers are small companies, start-ups and new companies.
Industry/Entity Type
Finance And Accounting
Contact Information for Business Card
Claireval Conseil et Comptes SA
Tomas Varenholt
Directeur et Fondateur
Expert-comptable diplômé
Tél. 022 418 57 34
tv@clairevalconseil.ch
www.clairevalconseil.ch
Rue des Vergières 27
1201 Genève

```html
<!DOCTYPE html>
<html lang="fr">
<head>
<meta charset="utf-8">
<title>Claireval Conseil et Comptes SA – Carte de visite</title>
<link href="https://fonts.googleapis.com/css2?family=Roboto:wght@400;500;700&display=swap" rel="stylesheet">
<style>
  :root {
    --backdrop: #e4e5e7;
    --card: #f7f8f8;
    --blue-light: #2fa3da;
    --blue-mid: #1f7fbd;
    --blue-dark: #15568f;
    --ink: #3a3d40;
    --ink-soft: #5b6066;
    --charcoal: #37393b;
  }
  * { margin: 0; padding: 0; box-sizing: border-box; }
  html, body { width: 1200px; height: 726px; overflow: hidden; }
  body {
    background: var(--backdrop);
    font-family: "Roboto", Arial, sans-serif;
    display: flex;
    align-items: center;
    justify-content: center;
    gap: 40px;
  }
  .card {
    position: relative;
    width: 520px;
    height: 300px;
    background: var(--card);
    box-shadow: 0 6px 18px rgba(0,0,0,.12);
    overflow: hidden;
  }
  .brand {
    display: flex;
    align-items: center;
    gap: 12px;
  }
  .brand-mark {
    width: 34px; height: 34px;
    background: var(--blue-mid);
    flex: none;
  }
  .brand-name {
    font-weight: 500;
    color: var(--ink);
    letter-spacing: .04em;
    line-height: 1.15;
  }

  /* Front */
  .card-front .brand {
    position: absolute;
    left: 0; right: 0; top: 108px;
    justify-content: center;
  }
  .card-front .brand-mark { width: 46px; height: 46px; }
  .card-front .brand-name { font-size: 24px; }
  .front-stripe {
    position: absolute;
    left: 0; right: 0; bottom: 0;
    height: 12px;
    background: linear-gradient(90deg, var(--blue-dark), var(--blue-light));
  }

  /* Back */
  .card-back .brand { position: absolute; left: 36px; top: 48px; }
  .card-back .brand-name { font-size: 19px; max-width: 260px; }
  .holder { position: absolute; left: 36px; top: 168px; }
  .holder-name {
    font-size: 20px; font-weight: 700;
    color: var(--blue-dark);
    margin-bottom: 6px;
  }
  .holder-role { font-size: 12.5px; color: var(--ink-soft); line-height: 1.4; }
  .contact {
    position: absolute; left: 300px; top: 92px;
    list-style: none;
  }
  .contact li {
    display: flex; align-items: center; gap: 10px;
    font-size: 12.5px; color: var(--ink);
    height: 20px;
  }
  .contact svg { width: 12px; height: 12px; fill: var(--blue-dark); flex: none; }
  .address-tab {
    position: absolute; right: 0; bottom: 12px;
    width: 290px; height: 40px;
    background: linear-gradient(90deg, var(--blue-dark), var(--blue-light));
    border-top-left-radius: 14px;
    color: #fff; font-size: 12.5px;
    display: flex; align-items: center; padding-left: 22px;
  }
  .base-strip {
    position: absolute; left: 0; right: 0; bottom: 0;
    height: 12px; background: var(--charcoal);
  }
</style>
</head>
<body>
  <section class="card card-front">
    <div class="brand">
      <span class="brand-mark"></span>
      <span class="brand-name">Claireval Conseil<br>et Comptes SA</span>
    </div>
    <div class="front-stripe"></div>
  </section>

  <section class="card card-back">
    <div class="brand">
      <span class="brand-mark"></span>
      <span class="brand-name">Claireval Conseil et Comptes SA</span>
    </div>

    <ul class="contact">
      <li>
        <svg viewBox="0 0 12 12"><path d="M1 4c0-2 2-3 5-3s5 1 5 3H8.5V3h-5v1zM2 5h8l1 6H1z"/></svg>
        022 418 57 34
      </li>
      <li>
        <svg viewBox="0 0 12 12"><path d="M0 2h12v1L6 7 0 3zM0 4.5l6 4 6-4V10H0z"/></svg>
        tv@clairevalconseil.ch
      </li>
      <li>
        <svg viewBox="0 0 12 12"><circle cx="6" cy="6" r="5.5"/><path d="M0.5 6h11M6 .5v11" stroke="#f7f8f8" stroke-width=".8"/></svg>
        www.clairevalconseil.ch
      </li>
    </ul>

    <div class="holder">
      <p class="holder-name">Tomas Varenholt</p>
      <p class="holder-role">Directeur et Fondateur<br>Expert-comptable diplômé</p>
    </div>

    <div class="address-tab">Rue des Vergières 27 1201 Genève</div>
    <div class="base-strip"></div>
  </section>
</body>
</html>
```